"Outside the Box" Newsletter Design Project-Communications Company

I am looking for an Internal newsletter for a communications company that will be sent to our sales and leadership team.
This newsletter will deliver forecasting, sales results, stack rankings for the sales reps, total team results, corporate updates, success stories and updates from Training/Operations/Sales/Marketing (could be a box for each)I would also need a couple sections with a blank header and box to add info as needed, if something comes up that is not set in stone weekly.
I am looking for a template that looks sharp and professional that i can use every week by just dropping content in, (text and possibly an employee picture) I will need it in a format (possibly word) that the will keep the text in line when I drop it in each week. Once complete I can save to a pdf and would like to have the ability to drop it into the body of an email.

We have a racecar theme that we use when training our sales folks so we would like a little bit of that to the newsletter and also incorporate our color scheme from our company.

I would like four versions of the newsletter..all would match other than the title.
1. Week 1 title - Start your engines
2. Week 2 title - Looking for suggestions
3. Week 3 title - Looking for suggestions
4. Week 4 title - Approaching the finish line, this version would also include an employee spotlight, one seperate section.

If we could include a few pics around racing that would be good, not over the top, just a few to give it a little of that feel. Maybe a checkered flag with the QV logo on it, a racecar..anything else that may make sense.

I will attach our logo and our organization is called SMB (small/medium business) so that should also be placed on there somewhere. Final design would need to be two pages, sharp professional feel, my Vice President likes a very clean look, not too busy. I have also attached a sample newsletter from another group in our company, ours will not have as much content, we are much smaller but this is a sample (on a smaller scale)of what we are looking for. The company look and feel is what we want to follow. Thank you

Target Market(s)

Our Internal sales team.

Industry/Entity Type

Communications

Requirements
Must have
• Ability to update with my content without having things shift and fall out of line..format that will make that easy and then able to save to PDF..2 pages long.
Nice to have
• HTML template to match.

```html
<!DOCTYPE html>
<html lang="en">
<head>
<meta charset="utf-8">
<title>QV Weekly Newsletter – Week 4</title>
<link href="https://fonts.googleapis.com/css2?family=Open+Sans:ital,wght@0,400;0,600;0,700;1,400&display=swap" rel="stylesheet">
<style>
:root{
  --page:#e8e8e8;
  --card:#ffffff;
  --ink:#333333;
  --muted:#6b6b6b;
  --rule:#dcdcdc;
  --purple:#7d3c98;
  --denver:#3b87c6;
  --houston:#4ca42f;
  --dallas:#e98a36;
  --chicago:#c9b71c;
  --row-alt:#f4f4f4;
}
*{box-sizing:border-box;margin:0;padding:0}
html,body{width:1200px;height:4688px;overflow:hidden}
body{background:var(--page);font-family:"Open Sans",Arial,sans-serif;color:var(--ink);position:relative}
.block{position:absolute;left:115px;width:970px}
.card{background:var(--card);box-shadow:0 2px 4px rgba(0,0,0,.08)}
p{font-size:18px;line-height:1.6;color:var(--muted)}
.btn{display:inline-block;border:2px solid #bdbdbd;border-radius:30px;padding:8px 34px;font-size:17px;line-height:1.3;color:var(--ink);background:#fff}

/* header */
.masthead{top:0;height:180px;display:flex;justify-content:space-between;align-items:center;padding:0 10px}
.brand-name{font-size:44px;font-weight:700;color:var(--ink)}
.issue{text-align:right}
.issue h2{font-size:24px;font-weight:700;color:var(--ink)}
.issue p{font-size:19px;line-height:1.4;color:var(--ink)}

/* hero */
.hero{top:200px;height:785px}
.hero-bar{height:72px;display:flex;justify-content:space-between;align-items:center}
.flag-tile{width:56px;height:72px;background:#777}
.hero-bar h1{font-size:28px;font-weight:700;color:#222}
.hero-photo{height:420px;background:linear-gradient(160deg,#2a1f3a,#6a5a8c 55%,#1d1d24)}
.hero-body{padding:28px 30px}
.hero-body p{margin-bottom:22px}

/* articles + events */
.articles{top:1005px;width:635px;height:590px;padding:0 30px}
.article{height:295px;padding-top:34px;display:grid;grid-template-columns:80px 1fr;gap:0 22px;align-content:start}
.article+.article{border-top:1px solid var(--rule)}
.date-badge{width:80px;height:80px;background:var(--purple);color:#fff;text-align:center;padding-top:8px}
.date-badge b{display:block;font-size:32px;line-height:1.1}
.date-badge span{font-size:14px;text-transform:uppercase}
.article h3{font-size:28px;font-weight:700;color:#222;line-height:1.2;margin-bottom:8px}
.article .btn{grid-column:2/3;justify-self:start;align-self:start;margin-top:20px}
.events{top:1005px;left:765px;width:320px;height:590px;padding:30px 22px;text-align:center}
.events h3{font-size:30px;font-weight:700;color:#222;text-align:left;margin-bottom:12px}
.event{padding:16px 0;border-top:1px solid var(--rule);font-size:18px;line-height:1.45}
.event .when{color:var(--purple)}

/* tables */
table{width:100%;border-collapse:collapse;font-size:18px}
th{background:var(--purple);color:#fff;text-align:left;font-weight:700;padding:0 30px}
td{padding:0 30px;color:var(--muted);border-bottom:1px solid var(--rule)}
.ranking{top:1640px;height:635px}
.ranking th{height:100px}
.ranking td{height:107px}
.ranking tr:nth-child(even) td{background:var(--row-alt)}
.teams{top:2320px;height:750px}
.teams th{height:90px}
.teams td{height:105px}
.team-band td{height:60px;color:#fff;font-weight:700;font-size:17px;border:0}
.denver td{background:var(--denver)}
.houston td{background:var(--houston)}
.dallas td{background:var(--dallas)}
.chicago td{background:var(--chicago)}

/* operations */
.ops{top:3115px;height:730px;padding:36px 30px;display:flex;gap:30px}
.portrait{flex:none;background:linear-gradient(170deg,#b9a699,#5d4a44 60%,#2d2a2c)}
.ops .portrait{width:300px;height:380px}
.ops h3,.story h3{font-size:30px;font-weight:700;color:#222;margin-bottom:12px}

/* success story */
.story{top:3890px;height:615px;padding:30px}
.story-top{display:flex;gap:26px;margin-top:6px}
.story .portrait{width:180px;height:225px}
.story h4{font-size:24px;font-weight:700;color:#222;margin-bottom:8px}
.story p{font-size:16px;line-height:1.55}
.story-bottom{display:flex;gap:26px;margin-top:20px}
.mini-table{flex:none;width:330px;border:1px solid var(--rule);font-size:11px;align-self:flex-start;margin-top:10px}
.mini-table th{background:var(--denver);padding:4px 6px;font-size:12px}
.mini-table td{padding:3px 6px;height:auto;font-size:11px}

/* footer */
.footer{top:4530px;height:130px;text-align:center;padding:0 30px}
.footer p{font-size:15px;font-style:italic;line-height:1.6;color:#888}
.footer a{color:var(--purple);font-weight:600;text-decoration:underline}
</style>
</head>
<body>

<header class="block masthead">
  <span class="brand-name">QV</span>
  <div class="issue">
    <h2>DECEMBER 20, 2012 ISSUE</h2>
    <p>A Weekly Recap of Important Things<br>Going on at QV That You Need To Know</p>
  </div>
</header>

<section class="block card hero">
  <div class="hero-bar">
    <div class="flag-tile" role="img" aria-label="Checkered flag corner"></div>
    <h1>WEEK 4 - Approaching the finish line</h1>
    <div class="flag-tile" role="img" aria-label="Checkered flag corner"></div>
  </div>
  <div class="hero-photo" role="img" aria-label="Close-up of a racing helmet"></div>
  <div class="hero-body">
    <p>Far far away, behind the word mountains, far from the countries Vokalia and Consonantia, there live the blind texts. Separated they live in Bookmarksgrove right at the coast of the Semantics, a large language ocean. A small river named Duden flows by their place and supplies it with the necessary regelialia. It is a paradisematic country, in which roasted parts of sentences fly into your mouth.</p>
    <span class="btn">Read More</span>
  </div>
</section>

<section class="block card articles">
  <article class="article">
    <div class="date-badge"><b>16</b><span>Aug</span></div>
    <div>
      <h3>Long Big Headline Title Here</h3>
      <p>Far far away, behind the word mountains, far from the countries Vokalia and Consonantia, there live the blind texts. Separated they live in</p>
    </div>
    <span class="btn">Read More</span>
  </article>
  <article class="article">
    <div class="date-badge"><b>16</b><span>Aug</span></div>
    <div>
      <h3>Long Big Headline Title Here</h3>
      <p>Far far away, behind the word mountains, far from the countries Vokalia and Consonantia, there live the blind texts. Separated they live in</p>
    </div>
    <span class="btn">Read More</span>
  </article>
</section>

<aside class="block card events">
  <h3>Upcoming Event</h3>
  <div class="event"><div class="when">Mon, July 23</div>CR Q2 Wrap-Up Presenta-<br>tion @ 3 pm</div>
  <div class="event"><div class="when">Fri, August 3</div>Chicago Mid-Year Town Hall</div>
  <div class="event"><div class="when">June 1—August 31</div>Double Down Challenge</div>
  <div class="event"><div class="when">June 1—August 31</div>CR Trusted To Handle Contest</div>
</aside>

<section class="block card ranking">
  <table>
    <tr><th>Rank</th><th>Sales Rep Name</th><th>Total MTD</th><th>Total Ptc</th></tr>
    <tr><td>1</td><td>Marlow, Evan T</td><td>USD $ 50,000</td><td>90%</td></tr>
    <tr><td>2</td><td>Marlow, Evan T</td><td>USD $ 40,000</td><td>80%</td></tr>
    <tr><td>3</td><td>Delgado, Nathan A</td><td>USD $ 38,000</td><td>70%</td></tr>
    <tr><td>4</td><td>Delgado, Nathan A</td><td>USD $ 20,000</td><td>60%</td></tr>
    <tr><td>5</td><td>Hollis, Grant J</td><td>USD $ 15,000</td><td>20%</td></tr>
  </table>
</section>

<section class="block card teams">
  <table>
    <tr><th>MTD Sales</th><th>MTD Ptc</th><th>July Points</th><th>June Points</th><th>Total Points</th></tr>
    <tr class="team-band denver"><td colspan="5">DENVER - TEAM BRENNER</td></tr>
    <tr><td>$ 40,000</td><td>80%</td><td>1</td><td>2</td><td>3</td></tr>
    <tr class="team-band houston"><td colspan="5">HOUSTON - TEAM CALDER</td></tr>
    <tr><td>$ 40,000</td><td>80%</td><td>1</td><td>2</td><td>3</td></tr>
    <tr class="team-band dallas"><td colspan="5">DALLAS - TEAM WHITLOCK</td></tr>
    <tr><td>$ 40,000</td><td>80%</td><td>1</td><td>2</td><td>3</td></tr>
    <tr class="team-band chicago"><td colspan="5">CHICAGO - TEAM SORENSEN</td></tr>
    <tr><td>$ 40,000</td><td>80%</td><td>1</td><td>2</td><td>3</td></tr>
  </table>
</section>

<section class="block card ops">
  <div class="portrait" role="img" aria-label="Employee photo holding a racing helmet"></div>
  <div>
    <h3>Updates from Operations</h3>
    <p>Far far away, behind the word mountains, far from the countries Vokalia and Consonantia, there live the blind texts. Separated they live in Bookmarksgrove right at the coast of the Semantics, a large language ocean. A small river named Duden flows by their place and supplies it with the necessary regelialia. It is a paradisematic country, in which roasted parts of sentences fly into your mouth. Even the all-powerful Pointing has no control about the blind texts it is an almost unorthographic life. One day however a small line of blind text by the name of Lorem Ipsum decided to leave for the far World of Grammar. The Big Oxmox advised her not to do so, because there were thousands of bad Commas, wild Question Marks and devious Semikoli, but the Little Blind Text didn't listen. She packed her seven versalia, put her</p>
  </div>
</section>

<section class="block card story">
  <h3>Success Story</h3>
  <div class="story-top">
    <div class="portrait" role="img" aria-label="Portrait of the featured employee"></div>
    <div>
      <h4>Say Hello For Marcus Hale From England.</h4>
      <p>Lorem ipsum dolor sit amet, consectetuer adipiscing elit. Aenean commodo ligula eget dolor. Aenean massa. Cum sociis natoque penatibus et magnis dis parturient montes, nascetur ridiculus mus. Donec quam felis, ultricies nec, pellentesque eu, pretium quis, sem. Nulla consequat massa quis enim. Donec pede justo, fringilla vel, aliquet nec, vulputate eget, arcu. In enim justo, rhoncus ut, imperdiet a, venenatis vitae, justo. Nullam dictum felis eu pede mollis pretium. Integer tincidunt. Cras dapibus.</p>
    </div>
  </div>
  <div class="story-bottom">
    <div>
      <h4>Marcus Hale Record?</h4>
      <p>Lorem ipsum dolor sit amet, consectetuer adipiscing elit. Aenean commodo ligula eget dolor. Aenean massa. Cum sociis natoque penatibus et magnis dis parturient montes, nascetur ridiculus mus. Donec quam felis, ultricies nec, pellentesque eu, pretium quis, sem. Nulla consequat massa quis enim. Donec pede justo, fringilla vel, aliquet nec, vulputate eget, arcu. In enim justo, rhoncus ut, imperdiet a, venenatis vitae, justo. Nullam dictum felis eu pede mollis pretium. Integer tincidunt. Cras dapibus.</p>
    </div>
    <table class="mini-table">
      <tr><th>Team</th><th>July</th><th>June</th><th>Total</th></tr>
      <tr><td>North</td><td>12</td><td>10</td><td>22</td></tr>
      <tr><td>South</td><td>9</td><td>11</td><td>20</td></tr>
      <tr><td>East</td><td>8</td><td>7</td><td>15</td></tr>
      <tr><td>West</td><td>6</td><td>9</td><td>15</td></tr>
      <tr><td>Central</td><td>5</td><td>6</td><td>11</td></tr>
      <tr><td>Metro</td><td>4</td><td>5</td><td>9</td></tr>
      <tr><td>Total</td><td>44</td><td>48</td><td>92</td></tr>
    </table>
  </div>
</section>

<footer class="block footer">
  <p>You are receiving this weekly update because you are part of the SMB sales and leadership team. Please keep the details in this issue internal and share questions with your team lead. Send content ideas for the next issue by Friday noon so they can be included. Thank you for your hard work this month and keep pushing toward the finish line. <a>Unsubscribe Newsletter Here</a></p>
</footer>

</body>
</html>
```